Marlow Dermal Studio - Business Banner with Brand Elements

Design:
• We would like to get a creative design for a wide banner that will go outside our medical spa clinic location. We need a designer to make a simple yet colorful and high-quality design layout. We want this banner to be eye-catching and to communicate the services we offer at our business: Laser Hair Removal | Veluxin | Lip Filler.

Requirements:
• We would like the banner to include our companies information which is the following:

Logo
“Refresh Your Skin”
Laser Hair Removal | Veluxin | Lip Filler
(520) 867-2291
www.MarlowDermalStudio.com

Colors:
• Our business colors are orange, a hint of black and white, but mostly peach/orange tones. (Orange: #f78f20 , White: #ffffff)

Fonts:
• Josefins Sans Bold & Lato

Content and images can be located here:
https://files.quibbleshare.com/share/folders/7tKwP3zRa9_LmQxVb2nD5yHc04EeJuFs8?mode=viewing

The following will give you an idea of our brand presentation:
• Our website is: www.MarlowDermalStudio.com
• Our Pictavo; @marlowdermalstudio
• Our Lumora: www.lumoranet.com/marlowdermalstudio

Target Market(s)
• Women 25 - 45

Industry/Entity Type
• Beauty

```html
<!DOCTYPE html>
<html lang="en">
<head>
<meta charset="utf-8">
<title>Marlow Dermal Studio – Banner Concepts</title>
<link href="https://fonts.googleapis.com/css2?family=Josefin+Sans:wght@600;700&family=Lato:wght@400;700&display=swap" rel="stylesheet">
<style>
  :root{
    --orange:#f78f20;
    --white:#ffffff;
    --ink:#111111;
    --board:#626262;
    --sky:#d7ebf4;
    --sea:#3cc2d5;
    --sea-light:#9fdfe2;
    --sand:#efdcc8;
    --sand-light:#f6e9dc;
  }
  *{margin:0;padding:0;box-sizing:border-box}
  html,body{width:1200px;height:572px;overflow:hidden;background:var(--board)}
  .board{position:relative;width:1200px;height:572px;background:var(--board)}
  .banner{position:absolute;width:533px;height:203px;overflow:hidden;background:var(--white)}
  .banner--beach-left{left:52px;top:65px}
  .banner--beach-right{left:613px;top:65px}
  .banner--duo-panel{left:52px;top:288px}
  .banner--duo-center{left:613px;top:298px}

  .photo{position:absolute}
  .photo--beach{background:linear-gradient(180deg,var(--sky) 0%,#e8f3f8 16%,var(--sea) 24%,var(--sea-light) 50%,#cfe7dd 60%,var(--sand) 72%,var(--sand-light) 100%)}
  .photo--shore{background:linear-gradient(180deg,#cfe4ef 0%,#e3eff5 30%,#7fd0da 45%,#d7ecec 60%,var(--sand) 78%,var(--sand-light) 100%)}
  .photo--city{background:linear-gradient(135deg,#8b8f7e 0%,#c9b7a3 35%,#b98a6a 60%,#e39a37 100%)}
  .photo--surf{background:linear-gradient(180deg,#62c9d3 0%,#8fd6dc 35%,#d6e6e4 60%,#e8ddd0 100%)}

  .logo{position:absolute;display:flex;align-items:center;gap:5px}
  .logo__mark{width:14px;height:14px;border-radius:50%;background:var(--orange);flex:none}
  .logo__name{font-family:"Josefin Sans",sans-serif;font-weight:700;color:var(--ink);font-size:13px;line-height:1;letter-spacing:.2px}
  .logo--stacked{flex-direction:column;gap:4px;text-align:center}
  .logo--stacked .logo__mark{width:22px;height:22px}

  .headline{position:absolute;font-family:"Josefin Sans",sans-serif;font-weight:700;color:var(--ink);line-height:1;white-space:nowrap}
  .headline--caps{text-transform:uppercase}

  .services{position:absolute;display:flex;align-items:center;gap:9px;font-family:"Josefin Sans",sans-serif;font-weight:700;text-transform:uppercase;white-space:nowrap}
  .services__item{display:flex;align-items:center;gap:3px}
  .services__dot{width:7px;height:7px;border-radius:50%;background:var(--orange)}

  .pill{position:absolute;background:var(--orange);color:var(--white);font-family:"Lato",sans-serif;font-weight:700;display:flex;align-items:center;justify-content:center;white-space:nowrap}

  .contact{position:absolute;font-family:"Lato",sans-serif;color:var(--ink);white-space:nowrap;display:flex;align-items:center;gap:5px}
  .icon{width:9px;height:9px;flex:none}

  .overlay{position:absolute;left:0;top:0}
</style>
</head>
<body>
<main class="board">

  <!-- Concept 1: full beach background, text left -->
  <section class="banner banner--beach-left">
    <div class="photo photo--beach" style="inset:0" role="img" aria-label="Smiling woman in a white bikini lying on a sunny beach with turquoise sea behind"></div>
    <div class="logo" style="left:29px;top:31px">
      <span class="logo__mark"></span>
      <span class="logo__name">Marlow<br>Dermal Studio</span>
    </div>
    <h1 class="headline headline--caps" style="left:29px;top:81px;font-size:24px">Refresh Your Skin</h1>
    <ul class="services" style="left:28px;top:113px;font-size:9.5px;color:var(--ink);list-style:none">
      <li class="services__item"><span class="services__dot"></span>Laser Hair Removal</li>
      <li class="services__item"><span class="services__dot"></span>Veluxin</li>
      <li class="services__item"><span class="services__dot"></span>Lip Filler</li>
    </ul>
    <div class="pill" style="left:28px;top:139px;width:226px;height:21px;border-radius:0 8px 8px 0;font-size:7.5px;font-weight:400;gap:12px">
      <span class="contact" style="position:static;color:var(--white);gap:4px">
        <svg class="icon" viewBox="0 0 10 10"><circle cx="5" cy="5" r="5" fill="#fff"/><path d="M3.2 2.6l1 .9-.5.8c.4.8.9 1.3 1.7 1.7l.8-.5.9 1-.7.8C4.8 7 3 5.2 2.6 3.3z" fill="#f78f20"/></svg>
        Phone: (520) 867-2291
      </span>
      <span class="contact" style="position:static;color:var(--white);gap:4px">
        <svg class="icon" viewBox="0 0 10 10" fill="none" stroke="#fff" stroke-width=".9"><circle cx="5" cy="5" r="4.3"/><ellipse cx="5" cy="5" rx="1.9" ry="4.3"/><path d="M.8 5h8.4M1.6 2.8h6.8M1.6 7.2h6.8"/></svg>
        www.MarlowDermalStudio.com
      </span>
    </div>
  </section>

  <!-- Concept 2: white panel left, curved photo right -->
  <section class="banner banner--beach-right">
    <div class="photo photo--beach" style="left:240px;top:0;right:0;bottom:0" role="img" aria-label="Smiling woman lying on the sand at the water's edge"></div>
    <svg class="overlay" width="533" height="203" viewBox="0 0 533 203" aria-hidden="true">
      <path d="M0 0H289Q238 100 286 203H0Z" fill="#f78f20"/>
      <path d="M0 0H281Q238 100 285 203H0Z" fill="#fff"/>
    </svg>
    <div class="logo" style="left:25px;top:20px">
      <span class="logo__mark" style="width:17px;height:17px"></span>
      <span class="logo__name" style="font-size:14px">Marlow<br>Dermal Studio</span>
    </div>
    <h1 class="headline headline--caps" style="left:27px;top:69px;font-size:20.5px">Refresh Your Skin</h1>
    <div class="pill" style="left:25px;top:95px;width:188px;height:25px;border-radius:13px;font-size:7.5px;letter-spacing:.3px">LASER HAIR REMOVAL | VELUXIN | LIP FILLER</div>
    <div class="contact" style="left:28px;top:136px;font-size:9px;font-weight:700">
      <svg class="icon" viewBox="0 0 10 10"><circle cx="5" cy="5" r="5" fill="#f78f20"/><path d="M3.2 2.6l1 .9-.5.8c.4.8.9 1.3 1.7 1.7l.8-.5.9 1-.7.8C4.8 7 3 5.2 2.6 3.3z" fill="#fff"/></svg>
      Phone: (520) 867-2291
    </div>
    <div class="contact" style="left:28px;top:156px;font-size:9px;font-weight:700">
      <svg class="icon" viewBox="0 0 10 10" fill="none" stroke="#f78f20" stroke-width=".9"><circle cx="5" cy="5" r="4.3"/><ellipse cx="5" cy="5" rx="1.9" ry="4.3"/><path d="M.8 5h8.4M1.6 2.8h6.8M1.6 7.2h6.8"/></svg>
      www.MarlowDermalStudio.com
    </div>
  </section>

  <!-- Concept 3: two photos framing a curved white center panel -->
  <section class="banner banner--duo-panel">
    <div class="photo photo--city" style="left:0;top:0;width:190px;height:203px" role="img" aria-label="Smiling woman with sunglasses on her head wearing an orange off-shoulder top"></div>
    <div class="photo photo--surf" style="left:350px;top:0;right:0;height:203px" role="img" aria-label="Woman in a striped bikini top with windswept hair by the sea"></div>
    <svg class="overlay" width="533" height="203" viewBox="0 0 533 203" aria-hidden="true">
      <path d="M166 0Q128 120 168 203" fill="none" stroke="#f78f20" stroke-width="1.6"/>
      <path d="M403 0Q432 70 378 203" fill="none" stroke="#f78f20" stroke-width="1.6"/>
      <path d="M172 0H394Q424 70 370 203H176Q136 120 172 0Z" fill="#fff"/>
    </svg>
    <div class="logo logo--stacked" style="left:208px;top:26px;width:110px">
      <span class="logo__mark"></span>
      <span class="logo__name" style="font-size:16px">Marlow<br>Dermal Studio</span>
    </div>
    <h1 class="headline" style="left:168px;top:102px;width:190px;text-align:center;font-size:22px">Refresh Your Skin</h1>
    <ul class="services" style="left:168px;top:129px;width:190px;justify-content:center;gap:6px;font-size:7px;color:var(--orange);list-style:none">
      <li class="services__item"><span class="services__dot" style="width:6px;height:6px"></span>Laser Hair Removal</li>
      <li class="services__item"><span class="services__dot" style="width:6px;height:6px"></span>Veluxin</li>
      <li class="services__item"><span class="services__dot" style="width:6px;height:6px"></span>Lip Filler</li>
    </ul>
    <div class="contact" style="left:160px;top:149px;width:206px;justify-content:center;font-size:7.2px">Phone: (520) 867-2291 &nbsp;|&nbsp; www.MarlowDermalStudio.com</div>
  </section>

  <!-- Concept 4: full shore background, centered text -->
  <section class="banner banner--duo-center">
    <div class="photo photo--shore" style="inset:0" role="img" aria-label="Two smiling women with windswept hair on a bright beach, one on each side"></div>
    <div class="logo" style="left:218px;top:29px">
      <span class="logo__mark" style="width:16px;height:16px"></span>
      <span class="logo__name" style="font-size:13.5px">Marlow<br>Dermal Studio</span>
    </div>
    <h1 class="headline" style="left:150px;top:76px;width:216px;text-align:center;font-size:25px">Refresh Your Skin</h1>
    <div class="pill" style="left:168px;top:109px;width:179px;height:23px;border-radius:12px;font-size:7px;letter-spacing:.3px">LASER HAIR REMOVAL | VELUXIN | LIP FILLER</div>
    <div class="contact" style="left:150px;top:143px;width:216px;justify-content:center;font-size:8.5px;font-weight:700">
      <svg class="icon" viewBox="0 0 10 10"><circle cx="5" cy="5" r="5" fill="#f78f20"/><path d="M3.2 2.6l1 .9-.5.8c.4.8.9 1.3 1.7 1.7l.8-.5.9 1-.7.8C4.8 7 3 5.2 2.6 3.3z" fill="#fff"/></svg>
      Phone: (520) 867-2291
    </div>
    <div class="contact" style="left:150px;top:162px;width:216px;justify-content:center;font-size:8.5px;font-weight:700">
      <svg class="icon" viewBox="0 0 10 10" fill="none" stroke="#f78f20" stroke-width=".9"><circle cx="5" cy="5" r="4.3"/><ellipse cx="5" cy="5" rx="1.9" ry="4.3"/><path d="M.8 5h8.4M1.6 2.8h6.8M1.6 7.2h6.8"/></svg>
      www.MarlowDermalStudio.com
    </div>
  </section>

</main>
</body>
</html>
```